Website for a high end London wedding DJ company

I want a website that is fairly basic but modern. It needs to look professional and smooth. I like white and black backgrounds. I am looking for something similar to this: https://www.torvalinsky.uk - at the bottom of this page it has ravenquill reviews as well. I mainly use bimmlo reviews. This would need to be included, or at least some way of showing all my 5 star reviews on the first page, to get peoples attention.
My current website is www.marrowandtide.com
My

1 page

• A way to display my reviews. Must be modern.
• Must not look cheesy and 8

```html
<!DOCTYPE html>
<html lang="en">
<head>
<meta charset="utf-8">
<title>Marrow and Tide — Wedding DJ Hire</title>
<link href="https://fonts.googleapis.com/css2?family=Cambo&family=Arimo:wght@400&display=swap" rel="stylesheet">
<style>
:root{
  --ink:#1a1a1a;
  --white:#ffffff;
  --paper:#f4f4f4;
  --mist:#e8e8e8;
  --night:#141414;
  --panel:#1f1f1f;
  --serif:'Cambo', Georgia, serif;
  --sans:'Arimo', Arial, sans-serif;
}
*{box-sizing:border-box;margin:0;padding:0}
html,body{width:1200px;height:5051px;overflow:hidden}
body{position:relative;background:var(--white);font-family:var(--serif);color:var(--ink)}
.abs{position:absolute}
.flourish{position:absolute;left:50%;transform:translateX(-50%);width:310px;height:10px;
  background:linear-gradient(90deg,transparent,rgba(120,120,120,.35) 20%,rgba(120,120,120,.35) 80%,transparent)}
.flourish.light{background:linear-gradient(90deg,transparent,rgba(255,255,255,.4) 20%,rgba(255,255,255,.4) 80%,transparent)}
.section-title{position:absolute;left:0;width:100%;text-align:center;font-family:var(--serif);text-transform:uppercase;letter-spacing:.5px;font-weight:400}

/* hero */
.hero{top:0;left:0;width:1200px;height:798px;
  background:
  radial-gradient(ellipse 22% 28% at 55% 18%,rgba(150,70,190,.85),transparent 75%),
  radial-gradient(ellipse 30% 30% at 15% 30%,rgba(120,90,70,.45),transparent 75%),
  radial-gradient(ellipse 35% 30% at 80% 60%,rgba(90,60,55,.5),transparent 75%),
  radial-gradient(ellipse 40% 30% at 35% 85%,rgba(70,45,40,.55),transparent 75%),
  linear-gradient(180deg,#2e1d33,#1e1619 55%,#151012)}
.brand{position:absolute;left:0;width:100%;text-align:center;font-family:var(--serif);color:var(--white)}
.hero .brand{top:44px;font-size:31px}
.main-nav{position:absolute;left:0;width:100%;display:flex;justify-content:center;gap:66px;font-size:14px;text-transform:uppercase;color:var(--white)}
.main-nav span:nth-child(2){text-transform:none}
.hero .main-nav{top:132px}
.hero-title{position:absolute;top:380px;width:100%;text-align:center;color:var(--white);font-size:82px;font-weight:400}
.hero-lead{position:absolute;top:496px;left:180px;width:840px;text-align:center;color:var(--white);font-size:15.5px;line-height:35px}

/* welcome */
.welcome-text{top:956px;left:230px;width:740px;text-align:center;font-size:13.5px;line-height:31px;color:#333}
.video{top:1096px;left:194px;width:812px;height:469px;background:
  radial-gradient(ellipse 18% 35% at 15% 55%,rgba(200,170,110,.45),transparent 75%),
  radial-gradient(ellipse 18% 30% at 42% 80%,rgba(235,235,240,.55),transparent 75%),
  radial-gradient(ellipse 20% 35% at 85% 60%,rgba(70,60,70,.6),transparent 75%),
  radial-gradient(ellipse 60% 20% at 50% 8%,rgba(90,70,110,.45),transparent 80%),
  linear-gradient(180deg,#1a1620,#2a2228 60%,#151215)}
.play{top:1298px;left:567px}

/* services */
.service{width:310px;height:467px;top:1641px;background:#000}
.service .shot{height:406px}
.service .label{height:61px;line-height:61px;text-align:center;color:var(--white);font-size:18px;text-transform:uppercase}

/* about */
.about{top:2196px;left:0;width:1200px;height:530px;background:var(--paper)}
.about-photo{top:0;left:0;width:653px;height:530px;background:
  radial-gradient(ellipse 22% 45% at 52% 62%,rgba(225,225,235,.75),transparent 75%),
  radial-gradient(ellipse 25% 40% at 85% 40%,rgba(140,100,60,.45),transparent 75%),
  radial-gradient(ellipse 25% 40% at 12% 35%,rgba(60,70,100,.6),transparent 75%),
  linear-gradient(160deg,#2f2a26,#1d2230 55%,#3a2f2a)}
.about-text{top:180px;left:720px;width:400px;text-align:center;font-family:var(--sans);font-size:13px;line-height:25px;color:#333}
.btn{top:412px;left:853px;width:133px;height:47px;border:2px solid var(--ink);border-radius:3px;text-align:center;line-height:43px;font-size:14px;text-transform:uppercase}

/* events */
.events{top:3624px;left:0;width:1200px;height:657px;background:var(--night)}
.track{width:474px;height:194px;background:var(--panel)}
.track .art{position:absolute;left:0;top:0;width:190px;height:194px}
.track .q{position:absolute;left:213px;top:24px;width:240px;color:var(--white);font-size:12.5px;line-height:26px;text-transform:uppercase}
.track .meta{position:absolute;left:213px;top:158px;width:240px;color:#ccc;font-size:12px;display:flex;justify-content:space-between;align-items:center}
.track svg.player{position:absolute;left:213px;top:82px}

/* testimonials */
.reviews{top:4281px;left:0;width:1200px;height:422px;background:var(--mist)}
.avatar{top:83px;left:173px;width:260px;height:260px;border-radius:50%;background:
  radial-gradient(ellipse 30% 45% at 50% 75%,rgba(230,230,238,.8),transparent 75%),
  radial-gradient(ellipse 40% 35% at 50% 15%,rgba(90,80,100,.6),transparent 80%),
  linear-gradient(160deg,#3a3430,#222a38 60%,#4a3c34)}
.quote-badge{top:308px;left:272px;width:56px;height:56px;border-radius:50%;background:var(--ink);color:var(--white);text-align:center;font-size:44px;line-height:66px}
.review-text{top:160px;left:486px;width:580px;font-size:13.5px;line-height:26px;color:#555;text-align:justify}
.reviewer{top:307px;left:486px;font-size:20px;color:#333}
.reviewer small{font-size:13px;color:#555}

/* footer */
.footer{top:4703px;left:0;width:1200px;height:348px;background:#000}
.footer .brand{top:66px;font-size:31px}
.footer .main-nav{top:160px}
.socials{top:220px;left:0;width:100%;display:flex;justify-content:center;gap:8px}
.socials span{width:36px;height:36px;border:2px solid var(--white);border-radius:50%}
.copyright{top:278px;width:100%;text-align:center;color:var(--white);font-size:15px}
</style>
</head>
<body>

<header class="abs hero" role="img" aria-label="Guests dancing with raised arms under purple lighting at a wedding reception">
  <div class="brand">Marrow &amp; Tide</div>
  <nav class="main-nav"><span>Home</span><span>DJs</span><span>Reviews</span><span>Gallery</span><span>Prices</span><span>About</span><span>Event Planner</span></nav>
  <h1 class="hero-title">Marrow and Tide</h1>
  <p class="hero-lead">With 13 years of experience in the DJing industry, we take care of the finer details to make planning your wedding day or special celebration a smooth and enjoyable experience.</p>
</header>

<div class="flourish" role="img" aria-label="decorative flourish" style="top:852px"></div>
<h2 class="section-title" style="top:880px;font-size:19px">Welcome to Marrow &amp; Tide</h2>
<div class="flourish" role="img" aria-label="decorative flourish" style="top:912px"></div>
<p class="abs welcome-text">Welcome to Marrow and Tide DJ hire Surrey. With 100% 5 star reviews on bimmlo, having only started in September 2019, we are fast becoming the number 1 DJ hire company in Surrey. Whether you are looking to book for weddings, birthday parties or any occasion full of fizz and dancing.</p>

<div class="abs video" role="img" aria-label="Video still of a bride and guests dancing under fairy lights in a marquee"></div>
<svg class="abs play" width="66" height="66" viewBox="0 0 66 66"><circle cx="33" cy="33" r="31" fill="rgba(0,0,0,.45)" stroke="#fff" stroke-width="2"/><path d="M26 20 L47 33 L26 46 Z" fill="#fff"/></svg>

<div class="abs service" style="left:112px"><div class="shot" role="img" aria-label="DJ behind a bar lit in purple with wine shelves behind" style="background:radial-gradient(ellipse 30% 18% at 50% 40%,rgba(220,215,220,.55),transparent 75%),radial-gradient(ellipse 60% 30% at 40% 85%,rgba(140,60,190,.8),transparent 80%),linear-gradient(180deg,#3a332c,#2a2230 50%,#3a1f4a)"></div><div class="label">DJs</div></div>
<div class="abs service" style="left:445px"><div class="shot" role="img" aria-label="Guests embracing on a purple-lit dance floor" style="background:radial-gradient(ellipse 35% 25% at 20% 15%,rgba(190,90,230,.9),transparent 75%),radial-gradient(ellipse 40% 30% at 55% 55%,rgba(120,80,90,.6),transparent 75%),linear-gradient(180deg,#5a2a78,#2a1a2e 55%,#151015)"></div><div class="label">Event Planner</div></div>
<div class="abs service" style="left:778px"><div class="shot" role="img" aria-label="Close-up of a DJ controller with glowing knobs and a jog wheel" style="background:radial-gradient(circle at 70% 78%,rgba(230,180,240,.95) 0,rgba(200,140,220,.6) 14%,transparent 26%),radial-gradient(ellipse 40% 30% at 30% 30%,rgba(120,100,170,.6),transparent 75%),linear-gradient(150deg,#2a2440,#3a2e5a 50%,#1e1828)"></div><div class="label">Others</div></div>

<section class="abs about">
  <div class="abs about-photo" role="img" aria-label="DJ in a white shirt at his decks in front of wine shelves"></div>
  <div class="flourish" role="img" aria-label="decorative flourish" style="left:920px;top:74px"></div>
  <h2 class="abs" style="top:90px;left:720px;width:400px;text-align:center;font-size:28px;font-weight:400;text-transform:uppercase">About Us</h2>
  <div class="flourish" role="img" aria-label="decorative flourish" style="left:920px;top:134px"></div>
  <p class="abs about-text">Growing up in a big family, parties were a regular occurence. Nights spent with loved ones full of dancing, fizz and laughter were some of our very first &amp; very best memories. Our adoration for these happy occasions full of love and music sparked our create this company. With Elliot's years of DJing experience, music has always been a big part of our life. We understand the importance of putting the music for your wedding day in the hands of the right people – people who you can trust, who experience and a vast knowledge of music.</p>
  <div class="abs btn">Read More</div>
</section>

<div class="flourish" role="img" aria-label="decorative flourish" style="top:2777px"></div>
<h2 class="section-title" style="top:2797px;font-size:29px">Photo Gallery</h2>
<div class="flourish" role="img" aria-label="decorative flourish" style="top:2840px"></div>

<div class="abs" role="img" aria-label="Bride dancing in a marquee under violet light" style="left:112px;top:2889px;width:314px;height:435px;background:radial-gradient(ellipse 28% 20% at 75% 15%,rgba(170,110,240,.95),transparent 75%),radial-gradient(ellipse 25% 25% at 45% 80%,rgba(235,200,220,.7),transparent 75%),linear-gradient(170deg,#3a2a40,#221a22 50%,#2a1e26)"></div>
<div class="abs" role="img" aria-label="Groom and guests laughing on the dance floor" style="left:443px;top:2889px;width:314px;height:209px;background:radial-gradient(ellipse 25% 45% at 25% 60%,rgba(200,190,210,.6),transparent 75%),radial-gradient(ellipse 25% 45% at 70% 65%,rgba(200,190,200,.5),transparent 75%),linear-gradient(150deg,#5a4a50,#2a2230)"></div>
<div class="abs" role="img" aria-label="Bride with raised arms among dancing guests" style="left:775px;top:2889px;width:313px;height:209px;background:radial-gradient(ellipse 25% 50% at 55% 60%,rgba(230,220,200,.65),transparent 75%),radial-gradient(ellipse 40% 40% at 20% 30%,rgba(170,90,120,.6),transparent 75%),linear-gradient(150deg,#4a2a42,#6a4a50)"></div>
<div class="abs" role="img" aria-label="Venue hall lit in blue with guests dancing" style="left:443px;top:3114px;width:645px;height:210px;background:radial-gradient(ellipse 20% 40% at 20% 35%,rgba(230,120,60,.55),transparent 75%),radial-gradient(ellipse 20% 40% at 85% 35%,rgba(230,120,60,.45),transparent 75%),radial-gradient(ellipse 25% 35% at 50% 25%,rgba(60,140,230,.75),transparent 75%),linear-gradient(180deg,#1d3a6a,#141a2e 60%,#1a1422)"></div>
<div class="abs" role="img" aria-label="Bride and guests dancing under fairy lights" style="left:112px;top:3340px;width:314px;height:206px;background:radial-gradient(ellipse 25% 35% at 60% 85%,rgba(240,240,245,.7),transparent 75%),radial-gradient(ellipse 60% 25% at 50% 10%,rgba(110,90,120,.6),transparent 80%),linear-gradient(150deg,#2a2a30,#3a2e38 50%,#2a2228)"></div>
<div class="abs" role="img" aria-label="Guests cheering under purple lights" style="left:443px;top:3340px;width:314px;height:206px;background:radial-gradient(ellipse 30% 35% at 45% 15%,rgba(200,110,240,.85),transparent 75%),radial-gradient(ellipse 40% 35% at 50% 80%,rgba(120,80,80,.55),transparent 75%),linear-gradient(150deg,#4a2a60,#2a1a26 60%,#1e1418)"></div>
<div class="abs" role="img" aria-label="Guests dancing beneath pink lighting in a barn" style="left:775px;top:3340px;width:313px;height:206px;background:radial-gradient(ellipse 30% 30% at 25% 15%,rgba(240,110,220,.85),transparent 75%),radial-gradient(ellipse 45% 40% at 65% 70%,rgba(210,120,200,.6),transparent 75%),linear-gradient(150deg,#6a2a62,#3a1e38 60%,#2a1a2a)"></div>

<section class="abs events">
  <div class="flourish light" role="img" aria-label="decorative flourish" style="top:38px"></div>
  <h2 class="section-title" style="top:58px;font-size:29px;color:var(--white)">Event Planner</h2>
  <div class="flourish light" role="img" aria-label="decorative flourish" style="top:100px"></div>
</section>

<div class="abs track" style="left:114px;top:3783px">
  <div class="art" role="img" aria-label="DJ in headphones at the decks" style="background:radial-gradient(ellipse 30% 45% at 50% 60%,rgba(230,230,235,.7),transparent 75%),linear-gradient(160deg,#6a5a48,#2a2a30)"></div>
  <div class="q">What are your most requested wedding songs?</div>
  <svg class="player" width="245" height="44" viewBox="0 0 245 44"><path d="M2 18h5l6-5v18l-6-5H2z" fill="#ccc"/><rect x="22" y="21" width="100" height="3" fill="#555"/><rect x="22" y="21" width="70" height="3" fill="#ddd"/><text x="132" y="27" fill="#ddd" font-size="13" font-family="Cambo, serif">00:55</text><line x1="178" y1="10" x2="178" y2="34" stroke="#555"/><circle cx="200" cy="22" r="17" fill="none" stroke="#fff" stroke-width="2"/><path d="M195 14 L208 22 L195 30 Z" fill="#fff"/></svg>
  <div class="meta"><span>▦ AUG 2021</span><span>◷ 00:56:02</span></div>
</div>
<div class="abs track" style="left:614px;top:3783px">
  <div class="art" role="img" aria-label="Singer in red light" style="background:radial-gradient(ellipse 35% 40% at 50% 35%,rgba(200,50,70,.8),transparent 75%),linear-gradient(160deg,#5a1420,#2a0a10)"></div>
  <div class="q">What are your most requested wedding songs?</div>
  <svg class="player" width="245" height="44" viewBox="0 0 245 44"><path d="M2 18h5l6-5v18l-6-5H2z" fill="#ccc"/><rect x="22" y="21" width="100" height="3" fill="#555"/><rect x="22" y="21" width="70" height="3" fill="#ddd"/><text x="132" y="27" fill="#ddd" font-size="13" font-family="Cambo, serif">00:55</text><line x1="178" y1="10" x2="178" y2="34" stroke="#555"/><circle cx="200" cy="22" r="17" fill="none" stroke="#fff" stroke-width="2"/><path d="M195 14 L208 22 L195 30 Z" fill="#fff"/></svg>
  <div class="meta"><span>▦ AUG 2021</span><span>◷ 00:56:02</span></div>
</div>
<div class="abs track" style="left:114px;top:4008px">
  <div class="art" role="img" aria-label="Guests dancing under purple light" style="background:radial-gradient(ellipse 35% 30% at 40% 20%,rgba(200,100,240,.85),transparent 75%),linear-gradient(160deg,#4a2a5a,#2a1a22)"></div>
  <div class="q">What are your most requested wedding songs?</div>
  <svg class="player" width="245" height="44" viewBox="0 0 245 44"><path d="M2 18h5l6-5v18l-6-5H2z" fill="#ccc"/><rect x="22" y="21" width="100" height="3" fill="#555"/><rect x="22" y="21" width="70" height="3" fill="#ddd"/><text x="132" y="27" fill="#ddd" font-size="13" font-family="Cambo, serif">00:55</text><line x1="178" y1="10" x2="178" y2="34" stroke="#555"/><circle cx="200" cy="22" r="17" fill="none" stroke="#fff" stroke-width="2"/><path d="M195 14 L208 22 L195 30 Z" fill="#fff"/></svg>
  <div class="meta"><span>▦ AUG 2021</span><span>◷ 00:56:02</span></div>
</div>
<div class="abs track" style="left:614px;top:4008px">
  <div class="art" role="img" aria-label="Blue-lit hall with a chandelier" style="background:radial-gradient(ellipse 30% 30% at 50% 35%,rgba(90,170,240,.8),transparent 75%),linear-gradient(160deg,#1d4a8a,#141a2e)"></div>
  <div class="q">What are your most requested wedding songs?</div>
  <svg class="player" width="245" height="44" viewBox="0 0 245 44"><path d="M2 18h5l6-5v18l-6-5H2z" fill="#ccc"/><rect x="22" y="21" width="100" height="3" fill="#555"/><rect x="22" y="21" width="70" height="3" fill="#ddd"/><text x="132" y="27" fill="#ddd" font-size="13" font-family="Cambo, serif">00:55</text><line x1="178" y1="10" x2="178" y2="34" stroke="#555"/><circle cx="200" cy="22" r="17" fill="none" stroke="#fff" stroke-width="2"/><path d="M195 14 L208 22 L195 30 Z" fill="#fff"/></svg>
  <div class="meta"><span>▦ AUG 2021</span><span>◷ 00:56:02</span></div>
</div>

<section class="abs reviews">
  <svg class="abs" style="left:58px;top:180px" width="26" height="100" viewBox="0 0 26 100"><path d="M24 2 L2 50 L24 98" fill="none" stroke="#bbb" stroke-width="2"/></svg>
  <svg class="abs" style="left:1112px;top:180px" width="26" height="100" viewBox="0 0 26 100"><path d="M2 2 L24 50 L2 98" fill="none" stroke="#bbb" stroke-width="2"/></svg>
  <div class="abs avatar" role="img" aria-label="Portrait of a client in a white shirt"></div>
  <div class="abs quote-badge">“</div>
  <div class="flourish" role="img" aria-label="decorative flourish" style="left:641px;top:70px"></div>
  <h2 class="abs" style="top:88px;left:486px;width:310px;text-align:center;font-size:29px;font-weight:400;text-transform:uppercase">Testimonials</h2>
  <div class="flourish" role="img" aria-label="decorative flourish" style="left:641px;top:128px"></div>
  <p class="abs review-text">Sed ut perspiciatis unde omnis iste natus error sit voluptatem accusantium doloremque laudantium, totam rem aperiam, eaque ipsa quae ab illo inventore veritatis et quasi architecto beatae vitae dicta sunt explicabo. Nemo enim ipsam voluptatem quia voluptas sit aspernatur aut odit aut fugit, sed quia consequuntur magni dolores eos qui ratione labore et dolore magnam omnis iste natus error sit aliquam quaerat voluptatem.</p>
  <div class="abs reviewer">Rowan Hale, <small>Sed ut perspiciatis unde</small></div>
</section>

<footer class="abs footer">
  <div class="brand">Marrow &amp; Tide</div>
  <nav class="main-nav"><span>Home</span><span>DJs</span><span>Reviews</span><span>Gallery</span><span>Prices</span><span>About</span><span>Event Planner</span></nav>
  <div class="abs socials" aria-label="Social links"><span></span><span></span><span></span><span></span></div>
  <p class="abs copyright">©2021 Marrow and Tide.All rights reserved.</p>
</footer>

</body>
</html>
```